Professional & attention grabbing.

A business card design, front and back. I already have a logo I will attach, but I am open to something new as well.
Things to include:
Name:
Title:
Phone:
Email:
Wanting something that is professional but attention grabbing.
Also we do a lot of work using drones on natural gas pipelines (leading the future)if you want to include any of that. I'm open to ideas.
Target Market(s)
Natural gas transmission industry / greenhouse gas mitigation industry
Industry/Entity Type
Business
Colors
Designer to choose colors to be used in the design.
Look and feel
Each slider illustrates characteristics of the customer's brand and the style your logo design should communicate.

```html
<!DOCTYPE html>
<html lang="en">
<head>
<meta charset="utf-8">
<title>Pipecrest Inspections – Business Card</title>
<link href="https://fonts.googleapis.com/css2?family=Open+Sans:ital,wght@0,400;0,600;0,700;1,400&display=swap" rel="stylesheet">
<style>
  :root {
    --page: #e4e4e4;
    --paper: #ffffff;
    --charcoal: #3a3a3c;
    --charcoal-light: #4b4b4d;
    --red: #c8202a;
    --ink: #3d3d3d;
    --white: #ffffff;
  }
  * { margin: 0; padding: 0; box-sizing: border-box; }
  html, body {
    width: 1200px; height: 987px; overflow: hidden;
    background: var(--page);
    font-family: "Open Sans", Arial, sans-serif;
  }
  .card {
    position: absolute; left: 293px; width: 615px; height: 352px;
    box-shadow: 0 2px 4px rgba(0,0,0,.18);
    overflow: hidden;
  }
  .card--front { top: 130px; background: var(--paper); }
  .card--back { top: 505px; background: var(--charcoal); }

  /* front */
  .brand {
    position: absolute; left: 33px; top: 40px;
    display: flex; align-items: center; gap: 12px;
  }
  .brand__square { width: 40px; height: 40px; background: var(--red); }
  .brand__name {
    font-weight: 700; font-size: 22px; line-height: 1.05;
    color: var(--charcoal); letter-spacing: .5px;
  }
  .contact {
    position: absolute; right: 26px; top: 196px; text-align: right;
    color: var(--ink);
  }
  .contact__name { color: var(--red); font-size: 21px; font-weight: 600; letter-spacing: .3px; }
  .contact__title { font-size: 16px; margin-top: 1px; }
  .contact__line {
    display: flex; justify-content: flex-end; align-items: center; gap: 8px;
    font-size: 15px; margin-top: 8px;
  }
  .contact__line + .contact__line { margin-top: 4px; }
  .contact__line svg { width: 14px; height: 14px; fill: var(--red); }
  .band-red {
    position: absolute; left: 0; bottom: 0; width: 380px; height: 10px;
    background: var(--red);
  }
  .band-dark { position: absolute; right: 0; bottom: 0; width: 255px; height: 36px; }
  .band-dark__text {
    position: absolute; right: 26px; bottom: 8px;
    color: var(--white); font-style: italic; font-size: 15px; letter-spacing: 2.4px;
  }

  /* back */
  .back-panel {
    position: absolute; left: 9px; top: 7px; width: 336px; height: 338px;
    background: var(--charcoal-light);
  }
  .back-brand {
    position: absolute; left: 374px; top: 178px;
    color: var(--white); font-weight: 700; font-size: 30px; line-height: 1.08;
    letter-spacing: .5px;
  }
  .back-web {
    position: absolute; left: 376px; top: 310px;
    color: var(--white); font-style: italic; font-size: 15px; letter-spacing: 2.4px;
  }
</style>
</head>
<body>
  <section class="card card--front">
    <div class="brand">
      <span class="brand__square"></span>
      <span class="brand__name">PIPECREST<br>INSPECTIONS</span>
    </div>

    <div class="contact">
      <div class="contact__name">DANA HALE</div>
      <div class="contact__title">CEO/FOUNDER</div>
      <div class="contact__line">555 214 7730
        <svg viewBox="0 0 24 24" aria-hidden="true"><path d="M6.6 10.8a15.1 15.1 0 0 0 6.6 6.6l2.2-2.2a1 1 0 0 1 1-.25 11.4 11.4 0 0 0 3.6.57 1 1 0 0 1 1 1V20a1 1 0 0 1-1 1A17 17 0 0 1 3 4a1 1 0 0 1 1-1h3.5a1 1 0 0 1 1 1c0 1.25.2 2.45.57 3.57a1 1 0 0 1-.25 1z"/></svg>
      </div>
      <div class="contact__line">dana@pipecrest.com
        <svg viewBox="0 0 24 24" aria-hidden="true"><path d="M2 5h20v14H2z" fill="var(--red)"/><path d="M2 5l10 8 10-8" fill="none" stroke="#fff" stroke-width="2"/></svg>
      </div>
    </div>

    <div class="band-red"></div>
    <svg class="band-dark" viewBox="0 0 255 36" preserveAspectRatio="none" aria-hidden="true">
      <polygon points="18,0 255,0 255,36 0,36" fill="var(--charcoal)"/>
    </svg>
    <div class="band-dark__text">www.pipecrest.com</div>
  </section>

  <section class="card card--back">
    <div class="back-panel"></div>
    <div class="back-brand">PIPECREST<br>INSPECTIONS</div>
    <div class="back-web">www.pipecrest.com</div>
  </section>
</body>
</html>
```